Flyer-Design für Heizungsbau
Zielgruppe
Wir sind ein junges, kompetentes und zertifiziertes Fachbetrieb und bieten Beratung, Fachplanung und fachmännische Installation von Wärmepumpen, Klimaanlagen und Lüftungsanlagen. Unsere Zielgruppe sind Eigentümer von Bestandsgebäuden oder Neubauten (hauptsächlich Privatkunden in mittlerem oder höherem Alter), welche eine Heizungssanierung für Heizkostenreduzierung oder neue Heizinstallation (Wärmepumpen), und/oder mehr Komfort bzw. Luftqualität in ihren Zuhause wünschen (Klima und Lüftung).
Aufgabenstellung
Schwerpunkte: 1. Ersparnis an Heizkosten, 2. Wohlgefühl und 3. Klimaschutz

```html
<!DOCTYPE html>
<html lang="de">
<head>
<meta charset="utf-8">
<title>Kühlwerk – Flyer</title>
<link href="https://fonts.googleapis.com/css2?family=Questrial&family=Roboto+Condensed:wght@300;400;700&display=swap" rel="stylesheet">
<style>
  :root{
    --navy:#0f3c7c;
    --sky:#3a96d8;
    --grey-text:#6b6b6b;
    --bg:#d6d6d8;
    --white:#ffffff;
    --band-a:#4aa3e0;
    --band-b:#bfe0f6;
  }
  *{margin:0;padding:0;box-sizing:border-box}
  html,body{width:1200px;height:2350px;overflow:hidden;background:var(--bg)}
  body{position:relative;font-family:"Questrial",sans-serif}
  .flyer{position:absolute;top:625px;width:550px;height:1100px;background:var(--white);overflow:hidden;box-shadow:0 4px 18px rgba(0,0,0,.18)}
  .flyer--front{left:30px}
  .flyer--back{left:620px}
  .abs{position:absolute}

  /* front */
  .headline{left:32px;top:34px;font-size:66px;line-height:62px;color:var(--sky);letter-spacing:.5px;font-weight:400}
  .headline .dark{color:var(--navy)}
  .product-photo{
    left:0;top:205px;width:550px;height:560px;
    background:
      radial-gradient(ellipse 38% 30% at 30% 46%, rgba(255,255,255,.95) 0%, rgba(248,248,249,.85) 45%, rgba(248,248,249,0) 100%),
      radial-gradient(ellipse 30% 20% at 68% 66%, rgba(255,255,255,.9) 0%, rgba(244,244,246,.7) 50%, rgba(244,244,246,0) 100%),
      radial-gradient(ellipse 70% 14% at 50% 86%, rgba(60,60,64,.35) 0%, rgba(60,60,64,0) 100%),
      radial-gradient(ellipse 85% 80% at 40% 50%, #cfcfd2 0%, #a3a3a7 50%, #6f6f73 85%, #5d5d61 100%);
  }
  .portrait-photo{left:339px;top:162px;width:216px;height:216px;border-radius:50%;background:radial-gradient(circle at 45% 40%,#e8d6a8 0%,#b59f6e 35%,#5b5040 70%,#2d2a26 100%)}
  .service{width:180px;text-align:center}
  .service__icon{width:110px;height:110px;border-radius:50%;background:var(--navy);margin:0 auto;display:flex;align-items:center;justify-content:center;box-shadow:0 3px 10px rgba(0,0,0,.25)}
  .service__title{font-size:29px;color:var(--navy);margin-top:14px}
  .service__text{font-family:"Roboto Condensed",sans-serif;font-weight:300;font-size:14px;line-height:18px;color:var(--grey-text);margin-top:6px;padding:0 12px}

  .tagline{left:30px;top:1023px;font-size:17px;line-height:19px;color:var(--navy)}
  .tagline span{color:var(--sky)}
  .brand{display:flex;align-items:center;gap:12px;font-size:38px;color:var(--sky)}
  .brand__dot{width:34px;height:34px;border-radius:50%;background:var(--sky)}

  /* back */
  .photo-strip-a{left:0;top:0;width:270px;height:205px;background:linear-gradient(135deg,#d9b48e 0%,#f1e9e4 50%,#b57a5c 100%)}
  .photo-strip-b{left:270px;top:0;width:280px;height:205px;background:linear-gradient(180deg,#bfc4c5 0%,#7c8584 55%,#5f7d48 100%)}
  .intro{left:28px;top:232px;width:496px;font-family:"Roboto Condensed",sans-serif;font-size:14.5px;line-height:24px;color:var(--navy)}
  .intro b{font-weight:700}
  .intro .hl{color:var(--sky)}
  .promise-title{left:28px;top:388px;font-size:27px;color:var(--sky);font-weight:400}
  .promise-list{left:28px;top:432px;width:250px;list-style:none}
  .promise-list li{margin-bottom:16px}
  .promise-list h3{font-weight:400;font-size:19.5px;color:var(--navy);line-height:24px}
  .promise-list p{font-family:"Roboto Condensed",sans-serif;font-weight:300;font-size:14.5px;line-height:19px;color:var(--sky)}
  .couple-photo{left:290px;top:406px;width:276px;height:276px;border-radius:50%;background:radial-gradient(circle at 50% 45%,#e8e4dd 0%,#a89b8c 55%,#5a4b42 100%)}
  .offer-band{left:0;top:753px;width:550px;height:240px;background:linear-gradient(90deg,var(--band-b) 0%,var(--band-a) 45%,var(--band-a) 100%)}
  .offer-circle{left:14px;top:747px;width:248px;height:248px;border-radius:50%;background:var(--white);box-shadow:0 0 18px rgba(255,255,255,.8)}
  .offer-call{left:40px;top:790px;width:180px;text-align:center;font-size:19px;line-height:21px;color:var(--sky);transform:rotate(-6deg)}
  .contact{left:28px;top:876px;font-size:17px;line-height:32px;color:var(--navy);transform:rotate(-6deg);transform-origin:left top}
  .contact div{display:flex;align-items:center;gap:8px}
  .benefits{left:292px;top:806px;list-style:none}
  .benefits li{display:flex;align-items:center;gap:10px;font-size:17px;color:var(--white);height:26px;margin-bottom:26px}
  .benefits li::before{content:"";width:16px;height:16px;border-radius:50%;border:2px solid var(--white)}
</style>
</head>
<body>

<section class="flyer flyer--front">
  <h1 class="abs headline"><span class="dark">Ihr Klima</span> ist<br>unser Anliegen!</h1>
  <div class="abs product-photo" role="img" aria-label="Foto: Wärmepumpe mit Innen- und Außengerät auf grauem Hintergrund"></div>
  <div class="abs portrait-photo" role="img" aria-label="Foto: lächelnde Frau mit Klimagerät"></div>

  <div class="abs service" style="left:15px;top:700px">
    <div class="service__icon">
      <svg width="58" height="58" viewBox="0 0 24 24"><path fill="#fff" d="M21.7 6.3a6 6 0 0 1-7.9 6.9L6.3 20.7a2.2 2.2 0 0 1-3-3l7.5-7.5A6 6 0 0 1 17.7 2.3l-3.5 3.5.4 3.6 3.6.4z"/></svg>
    </div>
    <div class="service__title">Installation</div>
    <p class="service__text">Wir installieren Ihre Klima&shy;anlage fachmännisch und mit höchster Präzision</p>
  </div>
  <div class="abs service" style="left:185px;top:700px">
    <div class="service__icon">
      <svg width="56" height="56" viewBox="0 0 24 24"><path fill="none" stroke="#fff" stroke-width="2.4" stroke-linejoin="round" d="M2 4h3l2.5 10h11L21 7H6.5"/><circle cx="9" cy="19" r="1.8" fill="#fff"/><circle cx="17" cy="19" r="1.8" fill="#fff"/></svg>
    </div>
    <div class="service__title">Verkauf</div>
    <p class="service__text">Bei uns erhalten Sie Ihr Klimagerät zu einem güns&shy;tigen Preis. Wir verkaufen nur hochwertige Anlagen</p>
  </div>
  <div class="abs service" style="left:355px;top:700px">
    <div class="service__icon">
      <svg width="58" height="58" viewBox="0 0 24 24"><path fill="#fff" d="M21.7 6.3a6 6 0 0 1-7.9 6.9L6.3 20.7a2.2 2.2 0 0 1-3-3l7.5-7.5A6 6 0 0 1 17.7 2.3l-3.5 3.5.4 3.6 3.6.4z"/></svg>
    </div>
    <div class="service__title">Wartung</div>
    <p class="service__text">Die notwendigen Wartungen an Ihrer Klimaanlage führen wir professionell durch</p>
  </div>

  <p class="abs tagline">Ihr Fachbetrieb für<br><span>Klimaanlagen und<br>Installation</span></p>
  <div class="abs brand" style="left:255px;top:1028px"><span class="brand__dot"></span>Kühlwerk</div>
</section>

<section class="flyer flyer--back">
  <div class="abs photo-strip-a" role="img" aria-label="Foto: Mann umarmt ein Klimagerät"></div>
  <div class="abs photo-strip-b" role="img" aria-label="Foto: modernes Haus mit Wärmepumpen-Außengerät"></div>

  <p class="abs intro">Kühlwerk GmbH ist Ihr zuverlässiger Partner im Bereich <b>Klima-, Kälte- und Lüftungstechnik</b>. Als <span class="hl">zertifiziertes Fachunternehmen</span> bieten wir Ihnen schlüsselfertige Kälte-, Klima- und Lüftungsanlagen von marktführenden Herstel&shy;lern. Von Installations- und Instandhaltungsleistungen bis zu Hygieneinspektio&shy;nen nach <b>VDI 6022</b> steht unser zertifiziertes Fachpersonal Ihnen gerne zur Seite.</p>

  <h2 class="abs promise-title">Unser Versprechen:</h2>
  <ul class="abs promise-list">
    <li><h3>Schnelle Installation</h3><p>Garantierte Installation innerhalb von wenigen Wochen</p></li>
    <li><h3>Festpreis</h3><p>Alle unsere Angebote zum Festpreiskeine Änderung durch mehr Aufwand</p></li>
    <li><h3>Faire Preise</h3><p>Wir sind von fairen Preisen überzeugt und bieten ein faires Preis-/Leistungsverhältnis</p></li>
    <li><h3>Höchste Qualität</h3><p>Wir führen jede Arbeit mit höchster Sorgfalt und Qualität durch</p></li>
  </ul>
  <div class="abs couple-photo" role="img" aria-label="Foto: Monteur bringt Klimagerät, Frau im Schlafzimmer"></div>

  <div class="abs offer-band"></div>
  <div class="abs offer-circle"></div>
  <p class="abs offer-call">Fordern Sie unverbindlich ein Angebot ein:</p>
  <div class="abs contact">
    <div><svg width="16" height="16" viewBox="0 0 24 24"><path fill="#0f3c7c" d="M6.6 10.8a15 15 0 0 0 6.6 6.6l2.2-2.2a1 1 0 0 1 1-.25 11.4 11.4 0 0 0 3.6.6 1 1 0 0 1 1 1V20a1 1 0 0 1-1 1A17 17 0 0 1 3 4a1 1 0 0 1 1-1h3.5a1 1 0 0 1 1 1 11.4 11.4 0 0 0 .6 3.6 1 1 0 0 1-.25 1z"/></svg>04521/7730412</div>
    <div><svg width="16" height="16" viewBox="0 0 24 24"><rect x="2" y="5" width="20" height="14" fill="#0f3c7c"/><path d="M2 5l10 8 10-8" fill="none" stroke="#fff" stroke-width="1.6"/></svg>info@kuehlwerk-service.de</div>
  </div>
  <ul class="abs benefits">
    <li>Ersparnis an Heizkosten</li>
    <li>Wohlgefühl</li>
    <li>Klimaschutz</li>
  </ul>

  <p class="abs tagline" style="top:1016px">Ihr Fachbetrieb für<br><span>Klimaanlagen und<br>Installation</span></p>
  <div class="abs brand" style="left:310px;top:1022px;font-size:32px"><span class="brand__dot" style="width:30px;height:30px"></span>Kühlwerk</div>
</section>

</body>
</html>
```